Design a homepage graphic to show a system journey

We have a software package for parents to update student information and manage school excursions we have attached a concept we like but are open to other ideas so long as they fit the following criteria.
1 It needs to be landscape across the page
2. They are showing a series of processes, each step has its own colour, see below
2.1 The first process is a parent updating their own and students information and approving excursions
2.2 The school then creates and manages the excursion this includes a compliance component
2.3 The school conducts the activity it should show some activity type pictures
2.4 Students return safely to school
3 There can be text boxes within the image to clarify functionality
4. The picture should make anyone watching it understand there is a series of
linked processes the system provides i.e. a journey
There should be the ability to click on each component to link to a specific part of the pager lower down, e.g if the person wanted to look at the school part by clicking on the school it would take them to more information, that information already exists so is not required.
Please review the attached concept diagram and use this a potential guide.
Schools
1 page

```html
<!DOCTYPE html>
<html lang="en">
<head>
<meta charset="utf-8">
<title>System Journey</title>
<link href="https://fonts.googleapis.com/css2?family=Poppins:wght@400;600;700&display=swap" rel="stylesheet">
<style>
:root{
  --step1:#14617a;
  --step2:#2fb4c6;
  --step3:#3fd3a2;
  --step4-pin:#c5e01f;
  --step4:#5cc41a;
  --step5:#f9a72b;
  --step6-pin:#e8393f;
  --step6:#3b3fd6;
  --road:#3a3a3c;
  --road-edge:#1f1f20;
  --ink:#111;
  --bg:#ffffff;
}
*{margin:0;padding:0;box-sizing:border-box}
html,body{width:1200px;height:530px;overflow:hidden;background:var(--bg)}
body{font-family:"Poppins",sans-serif;position:relative;
  background:radial-gradient(ellipse at 100% 0%,#eef0f3 0%,rgba(255,255,255,0) 35%),var(--bg)}
.journey-map{position:absolute;left:0;top:0}
.illustration{position:absolute;border-radius:10px}
.step{position:absolute;text-decoration:none;display:block}
.step-number{position:absolute;font-weight:400;line-height:1}
.step-title{position:absolute;font-weight:700;font-size:11px;white-space:nowrap;letter-spacing:.1px}
.step-body{position:absolute;font-size:6px;line-height:1.75;white-space:nowrap}
.step-1{color:var(--step1)} .step-2{color:var(--step2)} .step-3{color:var(--step3)}
.step-4{color:var(--step4)} .step-5{color:var(--step5)} .step-6{color:var(--step6)}
.step-body{opacity:.85}
.finish-label{position:absolute;left:986px;top:362px;font-weight:700;font-size:9.5px;color:var(--ink)}
</style>
</head>
<body>

<svg class="journey-map" width="1200" height="530" viewBox="0 0 1200 530" aria-label="Journey road from home to school">
  <defs>
    <filter id="pinShadow" x="-30%" y="-30%" width="160%" height="160%">
      <feDropShadow dx="1" dy="2" stdDeviation="2" flood-opacity=".25"/>
    </filter>
  </defs>

  <!-- road -->
  <g class="road" fill="none" stroke-linecap="round">
    <path d="M165 330 L230 330 C262 330 268 305 296 305 C330 305 360 347 395 347 C430 347 460 305 494 305 C528 305 558 347 593 347 C628 347 658 305 692 305 C726 305 756 347 791 347 C826 347 856 305 890 305 C920 305 930 330 960 330" stroke="var(--road-edge)" stroke-width="32"/>
    <path d="M165 330 L230 330 C262 330 268 305 296 305 C330 305 360 347 395 347 C430 347 460 305 494 305 C528 305 558 347 593 347 C628 347 658 305 692 305 C726 305 756 347 791 347 C826 347 856 305 890 305 C920 305 930 330 960 330" stroke="var(--road)" stroke-width="26"/>
    <path d="M165 330 L230 330 C262 330 268 305 296 305 C330 305 360 347 395 347 C430 347 460 305 494 305 C528 305 558 347 593 347 C628 347 658 305 692 305 C726 305 756 347 791 347 C826 347 856 305 890 305 C920 305 930 330 960 330" stroke="#fff" stroke-width="1.3" stroke-dasharray="6 5"/>
  </g>

  <!-- pins -->
  <a href="#parent-information">
    <g class="pin pin-1" filter="url(#pinShadow)">
      <path d="M284 245 L296 305 L308 245 Z" fill="var(--step1)"/>
      <circle cx="296" cy="225" r="32" fill="var(--step1)"/>
      <circle cx="296" cy="225" r="23" fill="#fff"/>
      <g fill="none" stroke="var(--step1)" stroke-width="1.3">
        <rect x="288" y="214" width="14" height="18" rx="1" transform="rotate(-12 295 223)"/>
        <rect x="292" y="215" width="14" height="18" rx="1" fill="#fff"/>
        <path d="M295 220h8M295 224h8M295 228h8"/>
      </g>
    </g>
  </a>
  <a href="#student-information">
    <g class="pin pin-2" filter="url(#pinShadow)">
      <path d="M383 290 L395 347 L407 290 Z" fill="var(--step2)"/>
      <circle cx="395" cy="270" r="32" fill="var(--step2)"/>
      <circle cx="395" cy="270" r="23" fill="#fff"/>
      <g fill="none" stroke="var(--step2)" stroke-width="1.3">
        <rect x="382" y="260" width="26" height="19" rx="2"/>
        <circle cx="389" cy="267" r="2.5"/>
        <path d="M385 275c1-3 7-3 8 0M396 266h8M396 270h8M396 274h6"/>
      </g>
    </g>
  </a>
  <a href="#approving-excursion">
    <g class="pin pin-3" filter="url(#pinShadow)">
      <path d="M482 245 L494 305 L506 245 Z" fill="var(--step3)"/>
      <circle cx="494" cy="225" r="32" fill="var(--step3)"/>
      <circle cx="494" cy="225" r="23" fill="#fff"/>
      <circle cx="494" cy="225" r="14" fill="none" stroke="var(--step3)" stroke-width="1.5"/>
      <rect x="480" y="220" width="28" height="10" fill="#fff" stroke="var(--step3)" stroke-width="1"/>
      <text x="494" y="228" text-anchor="middle" font-family="Poppins,sans-serif" font-weight="700" font-size="5.6" fill="var(--step3)">APPROVED</text>
    </g>
  </a>
  <a href="#school-accepts-update">
    <g class="pin pin-4" filter="url(#pinShadow)">
      <path d="M581 290 L593 347 L605 290 Z" fill="var(--step4-pin)"/>
      <circle cx="593" cy="270" r="32" fill="var(--step4-pin)"/>
      <circle cx="593" cy="270" r="23" fill="#fff"/>
      <circle cx="593" cy="270" r="8.5" fill="none" stroke="var(--step4-pin)" stroke-width="1.3"/>
      <path d="M589 270l3 3 5-6" fill="none" stroke="var(--step4-pin)" stroke-width="1.3" stroke-linecap="round"/>
    </g>
  </a>
  <a href="#school-takes-excursion">
    <g class="pin pin-5" filter="url(#pinShadow)">
      <path d="M680 245 L692 305 L704 245 Z" fill="var(--step5)"/>
      <circle cx="692" cy="225" r="32" fill="var(--step5)"/>
      <circle cx="692" cy="225" r="23" fill="#fff"/>
      <path d="M678 224l6-5 6 2 4-2 6 4 2 4-6 3-5 2-6-3z" fill="none" stroke="var(--step5)" stroke-width="1.3" stroke-linejoin="round"/>
    </g>
  </a>
  <a href="#school-conduct-activity">
    <g class="pin pin-6" filter="url(#pinShadow)">
      <path d="M779 290 L791 347 L803 290 Z" fill="var(--step6-pin)"/>
      <circle cx="791" cy="270" r="32" fill="var(--step6-pin)"/>
      <circle cx="791" cy="270" r="23" fill="#fff"/>
      <g fill="var(--step6-pin)">
        <rect x="782" y="272" width="3.5" height="8"/>
        <rect x="787" y="268" width="3.5" height="12"/>
        <rect x="792" y="273" width="3.5" height="7"/>
        <rect x="797" y="266" width="3.5" height="14"/>
      </g>
      <path d="M781 270l6-6 5 4 8-8" fill="none" stroke="var(--step6-pin)" stroke-width="1.4"/>
      <path d="M797 259l4 0 0 4z" fill="var(--step6-pin)"/>
    </g>
  </a>
</svg>

<!-- start and finish -->
<a class="step home" href="#parent-information">
  <div class="illustration" role="img" aria-label="Family home with garden fence" style="left:30px;top:242px;width:166px;height:126px;background:linear-gradient(180deg,#f8b62a 0%,#f39a1e 70%,#72a844 100%)"></div>
</a>
<a class="step school" href="#students-return">
  <div class="illustration" role="img" aria-label="School building with children returning" style="left:953px;top:228px;width:170px;height:129px;background:linear-gradient(180deg,#d93a31 0%,#f3a525 45%,#f7b22f 100%)"></div>
</a>
<div class="finish-label" id="students-return">STUDENTS RETURN SCHOOL</div>

<!-- step 1 -->
<a class="step step-1" href="#parent-information">
  <div class="illustration" role="img" aria-label="Parents helping child at laptop" style="left:242px;top:51px;width:80px;height:86px;background:linear-gradient(180deg,#f6c4a6,#d8493e 60%,#b0652d)"></div>
</a>
<div class="step-number step-1" style="left:203px;top:138px;font-size:50px">1</div>
<div class="step-title step-1" style="left:228px;top:144px">PARENT INFORMATION</div>
<div class="step-body step-1" style="left:228px;top:160px">Excepteur sint occaecat cupidatat non<br>officia deserunt mollit anim id est laborum.</div>

<!-- step 3 -->
<a class="step step-3" href="#approving-excursion">
  <div class="illustration" role="img" aria-label="Approved form beside a young explorer" style="left:445px;top:47px;width:100px;height:90px;background:linear-gradient(90deg,#eef3f2 0%,#e4ecea 40%,#c89a58 70%,#8a4b3a)"></div>
</a>
<div class="step-number step-3" style="left:418px;top:140px;font-size:46px">3</div>
<div class="step-title step-3" style="left:453px;top:142px">APPROVING EXCURSION</div>
<div class="step-body step-3" style="left:453px;top:157px">Excepteur sint occaecat cupidatat non<br>officia deserunt mollit anim id est laborum.</div>

<!-- step 5 -->
<a class="step step-5" href="#school-takes-excursion">
  <div class="illustration" role="img" aria-label="Yellow school bus" style="left:674px;top:83px;width:80px;height:52px;background:linear-gradient(180deg,#fcd21c,#f3b712 75%,#5a3c48)"></div>
</a>
<div class="step-number step-5" style="left:673px;top:140px;font-size:36px">5</div>
<div class="step-title step-5" style="left:699px;top:142px">SCHOOL TAKES&nbsp; TO THE&nbsp; EXCURSION</div>
<div class="step-body step-5" style="left:699px;top:158px">Quis autem vel eum iure reprehenderit qui in ea voluptate<br>&nbsp;velit esse quam</div>

<!-- step 2 -->
<a class="step step-2" href="#student-information">
  <div class="illustration" role="img" aria-label="Student sitting with laptop, books and backpack" style="left:340px;top:370px;width:114px;height:87px;background:linear-gradient(180deg,#c56a3a,#a640b5 55%,#dcdcdc)"></div>
</a>
<div class="step-number step-2" style="left:313px;top:458px;font-size:46px">2</div>
<div class="step-title step-2" style="left:348px;top:463px">STUDENT INFORMATION</div>
<div class="step-body step-2" style="left:348px;top:478px">Excepteur sint occaecat cupidatat non<br>officia deserunt mollit anim id est laborum.</div>

<!-- step 4 -->
<a class="step step-4" href="#school-accepts-update">
  <div class="illustration" role="img" aria-label="School building with update banner" style="left:541px;top:377px;width:123px;height:80px;background:linear-gradient(180deg,#d93a31,#f1a524 50%,#5cc41a)"></div>
</a>
<div class="step-number step-4" style="left:532px;top:460px;font-size:40px">4</div>
<div class="step-title step-4" style="left:561px;top:463px">SCHOOL ACCEPTS ALL THE UPDATE</div>
<div class="step-body step-4" style="left:561px;top:478px;font-size:4.6px">Excepteur sint occaecat cupidatat non officia deserunt mollit<br>anim id est laborum.</div>

<!-- step 6 -->
<a class="step step-6" href="#school-conduct-activity">
  <div class="illustration" role="img" aria-label="School with trees and children arriving by bus" style="left:788px;top:368px;width:98px;height:91px;background:linear-gradient(180deg,#8fd3e0,#e8e4dc 40%,#3c8b3c 70%,#f2a81c)"></div>
</a>
<div class="step-number step-6" style="left:762px;top:460px;font-size:40px">6</div>
<div class="step-title step-6" style="left:792px;top:463px">SCHOOL CONDUCT ACTIVITY</div>
<div class="step-body step-6" style="left:792px;top:478px;font-size:4.6px">Excepteur sint occaecat cupidatat non officia deserunt mollit<br>anim id est laborum.</div>

</body>
</html>
```